Venture Capital firm needs modern business cards

We are a Venture Capital firm within financial services/Asset management. The industry generally has basic business cards with black, blue and maybe green/yellow design elements.
Our firm has a four-colour swoosh logo. We are based in London and want to stand out, just a little bit!, from the crowd. Our company is called LORV Investments and the 'C' stands for collaboration thus using makerswarm is a natural portal for our business card design competition. Our logo came via makerswarm too!
We use 'Venture Partner in Asset Management' as our tagline and this is Trademark registered. We operate in a conservative industry and we should not overstep our mark. The logo is colorful as it is and therefore the rest of the design should not be too fanciful.
The objective is twofold: make our logo element stick and memorable with our audience, whilst representing a conservative yet young image.
Updates
The Business Card obviously needs a field for Name, Surname, Job Title, Adress fields: Street, City, Postcode, Country, telefone and cell number, website address, etc.
We have uploaded the ai file. We trust that these are OK. If not, please advise.
Reason: We have have been busy with a client engagement. We will set the project as Guaranteed in return for the troubles we cause. Apologies for the confusion.
Thank you all for these great and creative design suggestions. The team is very happy with a number of your ideas! We will be in touch tomorrow to give individual feedback before the project closes on Friday. We look forward to working with some of you to narrow down your creations. Thank you, LORV Investments team.
All,
Target Market(s)
Financial Services Professionals, Investors, Media, 35-70 years, mainly male, well educated
Industry/Entity Type
Conservative
Requirements
Must have
- We must make use of our logo and potential tagline 'Venture Partner in Asset Management' as we are establishing a new Brand and new company in the market.
We can use 'LORV', 'LORV Investments', and 'LORV Investments'+tagline 'Venture Partner in Asset Management' or simply the four-colour swoosh plus the name of the company as part of the text. (see files)
All design elements are available in black or grey-scale if required. (grey scale swoosh attached).
Due to regulation we must have the following wording on the card in small print 'LORV Investments is an Appointed Representative of Bramwell Holdings Partnership Limited, which is authorised by the Monetary Oversight Board'.
Nice to have
- We would consider designs that make use of different printing techniques such embossing/debossing, UV spot etc.
We attach our colour palette in the files section for your reference.
Should not have
- The font we use for our company name is 'EXO' so do not use a font style that clashes with the corporate fonts, please.
Do not use other design elements than the ones we provide in the file library as part of this project.

```html
<!DOCTYPE html>
<html lang="en">
<head>
<meta charset="UTF-8">
<title>LORV Investments — Business Card</title>
<link href="https://fonts.googleapis.com/css2?family=Exo:wght@200;300;500&family=Roboto+Condensed:wght@300;400&display=swap" rel="stylesheet">
<style>
  :root {
    --backdrop: #9b9b9b;
    --card: #ffffff;
    --ink-dark: #3b3d3f;
    --ink-mid: #7b7d80;
    --ink-tagline: #2e3033;
    --accent-green: #8cc63f;
  }
  * { box-sizing: border-box; margin: 0; padding: 0; }
  html, body {
    width: 1200px; height: 487px; overflow: hidden;
    background: var(--backdrop);
  }
  .canvas { position: relative; width: 1200px; height: 487px; }
  .card {
    position: absolute; top: 80px; height: 326px;
    background: var(--card); border-radius: 30px;
  }
  .card--front { left: 53px; width: 530px; }
  .card--back { left: 607px; width: 541px; }

  /* Front */
  .brand {
    position: absolute; top: 56px; left: 0; width: 100%;
    display: flex; align-items: center; justify-content: center; gap: 14px;
  }
  .brand__dot {
    width: 22px; height: 22px; border-radius: 50%;
    background: var(--accent-green);
  }
  .brand__name {
    font-family: "Exo", sans-serif; font-weight: 500;
    font-size: 46px; color: var(--ink-dark); letter-spacing: 1px;
  }
  .holder {
    position: absolute; top: 176px; left: 0; width: 100%; text-align: center;
    font-family: "Roboto Condensed", sans-serif;
  }
  .holder__name { font-size: 17px; color: var(--ink-mid); font-weight: 400; letter-spacing: .3px; }
  .holder__title { font-size: 14px; color: var(--accent-green); margin-top: 3px; font-weight: 400; }
  .contact {
    position: absolute; top: 256px; left: 0; width: 100%; text-align: center;
    font-family: "Roboto Condensed", sans-serif; font-weight: 300;
    font-size: 13.5px; color: var(--ink-mid); line-height: 18.5px;
  }
  .contact__line { display: flex; justify-content: center; align-items: center; gap: 6px; }
  .contact__item { display: inline-flex; align-items: center; gap: 5px; margin: 0 4px; }
  .icon { width: 12px; height: 12px; fill: var(--accent-green); }

  /* Back */
  .tagline {
    position: absolute; font-family: "Exo", sans-serif; font-weight: 200;
    color: var(--ink-tagline); line-height: 1; white-space: nowrap;
  }
  .tagline--venture { left: 156px; top: 68px; font-size: 31px; }
  .tagline--partner { left: 154px; top: 100px; font-size: 54px; }
  .tagline--in { left: 180px; top: 168px; font-size: 22px; }
  .tagline--asset { left: 203px; top: 147px; font-size: 54px; }
  .tagline--management { left: 199px; top: 196px; font-size: 30px; }
  .web {
    position: absolute; left: 200px; top: 239px;
    font-family: "Roboto Condensed", sans-serif; font-size: 14.5px;
    color: var(--ink-mid); font-weight: 400;
  }
  .web__domain { color: var(--accent-green); font-weight: 400; }
</style>
</head>
<body>
<main class="canvas">
  <section class="card card--front" aria-label="Card front">
    <div class="brand">
      <span class="brand__dot" aria-hidden="true"></span>
      <span class="brand__name">LORV Investments</span>
    </div>
    <div class="holder">
      <p class="holder__name">CARDHOLDER NAME</p>
      <p class="holder__title">Designation</p>
    </div>
    <div class="contact">
      <p class="contact__line">
        <span class="contact__item">
          <svg class="icon" viewBox="0 0 12 12" aria-hidden="true"><path d="M6 0a4 4 0 0 0-4 4c0 3 4 8 4 8s4-5 4-8a4 4 0 0 0-4-4zm0 5.6A1.6 1.6 0 1 1 6 2.4a1.6 1.6 0 0 1 0 3.2z"/></svg>
          0101 Avenue, Suite No. 123, Your City, Country
        </span>
      </p>
      <p class="contact__line">
        <span class="contact__item">
          <svg class="icon" viewBox="0 0 12 12" aria-hidden="true"><circle cx="6" cy="6" r="6"/><path d="M4 3l1.2 1.5-.6.8a4 4 0 0 0 2 2l.8-.6L9 8l-.8 1C5.5 9 3 6.5 3 3.8z" fill="#fff"/></svg>
          +012 345 6789
        </span>
        <span class="contact__item">
          <svg class="icon" viewBox="0 0 12 12" aria-hidden="true"><rect x="3" y="0" width="6" height="4"/><rect x="0" y="5" width="12" height="6" rx="1"/><rect x="2" y="7" width="3" height="1" fill="#fff"/></svg>
          +012 345 6780
        </span>
      </p>
      <p class="contact__line">
        <span class="contact__item">
          <svg class="icon" viewBox="0 0 14 10" style="width:14px;height:10px" aria-hidden="true"><rect width="14" height="10" rx="1"/><g fill="#fff"><rect x="2" y="2" width="2" height="1.5"/><rect x="5" y="2" width="2" height="1.5"/><rect x="8" y="2" width="2" height="1.5"/><rect x="11" y="2" width="1.5" height="1.5"/><rect x="3" y="6.5" width="8" height="1.5"/></g></svg>
          cardholder.name@lorvinvestments.com
        </span>
      </p>
    </div>
  </section>

  <section class="card card--back" aria-label="Card back">
    <span class="tagline tagline--venture">Venture</span>
    <span class="tagline tagline--partner">Partner</span>
    <span class="tagline tagline--in">in</span>
    <span class="tagline tagline--asset">Asset</span>
    <span class="tagline tagline--management">Management</span>
    <p class="web">www.<span class="web__domain">lorvinvestments</span>.com</p>
  </section>
</main>
</body>
</html>
```